Specialised investor in e-mobility and energy wants business card design

We need a business card design that fits our existing corporate design. <The look and feel must be 'sharp'/'clean', dynamic, communicate momentum, professionalism etc (as one would imagine from a firm in the financial sector). We like the idea of a reverse-side of the card that includes the logo, and the name and contact details on the other. We expect the deliverable to be whatever format might be required to be able to get cards printed directly by a service such as kelmo press. Our website is www.zub.capital

```html
<!DOCTYPE html>
<html lang="en">
<head>
<meta charset="utf-8">
<title>ZUB Capital – Business Card</title>
<link href="https://fonts.googleapis.com/css2?family=Montserrat:wght@500;700&family=Nunito+Sans:wght@400&display=swap" rel="stylesheet">
<style>
  :root {
    --backdrop: #1f1f1f;
    --card-white: #ffffff;
    --green-dark: #344f24;
    --green-light: #8ab54a;
    --text-grey: #2f2f2f;
  }
  * { margin: 0; padding: 0; box-sizing: border-box; }
  html, body {
    width: 1200px; height: 1059px; overflow: hidden;
    background: var(--backdrop);
  }
  .canvas { position: relative; width: 1200px; height: 1059px; }
  .card {
    position: absolute;
    border-radius: 15px;
    overflow: hidden;
  }
  .card-front {
    left: 257px; top: 89px; width: 687px; height: 390px;
    background: var(--card-white);
  }
  .card-back {
    left: 254px; top: 547px; width: 693px; height: 393px;
    background: var(--green-dark);
    display: flex; align-items: center; justify-content: center;
  }
  .front-wave { position: absolute; left: 0; top: 0; width: 687px; height: 390px; }
  .brand-name {
    font-family: 'Montserrat', sans-serif;
    font-weight: 500;
    letter-spacing: 0.5px;
    white-space: nowrap;
    line-height: 1;
  }
  .card-front .brand-name {
    position: absolute; left: 36px; top: 60px;
    font-size: 47px; color: var(--green-dark);
  }
  .card-back .brand-name {
    font-size: 88px; color: var(--card-white);
  }
  .holder {
    position: absolute; right: 36px; top: 171px; text-align: right;
  }
  .holder-name {
    font-family: 'Montserrat', sans-serif; font-weight: 700;
    font-size: 26px; letter-spacing: 1px; color: var(--green-dark); line-height: 1;
  }
  .holder-name .surname { color: var(--green-light); }
  .holder-role {
    font-family: 'Nunito Sans', sans-serif; font-size: 16px;
    color: var(--text-grey); margin-top: 6px; letter-spacing: 0.4px;
  }
  .contact {
    position: absolute; left: 35px; top: 197px;
    font-family: 'Nunito Sans', sans-serif; font-size: 16px;
    color: var(--text-grey); letter-spacing: 0.5px;
  }
  .address { line-height: 22px; margin-bottom: 10px; white-space: nowrap; }
  .contact-line { display: flex; align-items: center; height: 27px; white-space: nowrap; }
  .contact-line svg { width: 12px; height: 12px; margin-right: 7px; flex: none; }
</style>
</head>
<body>
<div class="canvas">
  <section class="card card-front">
    <svg class="front-wave" viewBox="0 0 687 390" aria-hidden="true">
      <path d="M0,328 C40,362 100,368 200,366 C330,362 420,318 540,314 C610,312 665,322 687,342 L687,390 L0,390Z" fill="#8ab54a"/>
      <path d="M0,334 C40,366 100,372 200,370 C300,368 400,330 520,324 C600,320 660,330 687,356" fill="none" stroke="#ffffff" stroke-width="3"/>
      <path d="M0,336 C40,368 100,374 200,372 C300,370 400,332 520,326 C600,322 660,332 687,358 L687,390 L0,390Z" fill="#344f24"/>
    </svg>
    <div class="brand-name">ZUB Capital</div>
    <div class="holder">
      <div class="holder-name">MARTIN <span class="surname">OLVER</span></div>
      <div class="holder-role">Director/Founder</div>
    </div>
    <div class="contact">
      <div class="address">5870 Harbor Lane<br>Region Name CD 4129</div>
      <div class="contact-line">
        <svg viewBox="0 0 24 24"><path fill="#8ab54a" d="M6.6 10.8a15 15 0 0 0 6.6 6.6l2.2-2.2a1 1 0 0 1 1-.25 11.4 11.4 0 0 0 3.6.57 1 1 0 0 1 1 1V20a1 1 0 0 1-1 1A17 17 0 0 1 3 4a1 1 0 0 1 1-1h3.5a1 1 0 0 1 1 1c0 1.25.2 2.45.57 3.6a1 1 0 0 1-.25 1z"/></svg>
        987-402-3318
      </div>
      <div class="contact-line">
        <svg viewBox="0 0 24 24"><path fill="#8ab54a" d="M2 5h20v14H2z"/><path fill="none" stroke="#fff" stroke-width="2" d="M2 6l10 7 10-7"/></svg>
        info@zub.capital
      </div>
      <div class="contact-line">
        <svg viewBox="0 0 24 24"><circle cx="12" cy="12" r="10" fill="#8ab54a"/><path fill="#fff" d="M7 6c2 0 3 2 2 4s-3 1-4 3c-1-3 0-6 2-7zm8 6c2 0 3 2 2 4s-3 3-4 2 0-6 2-6z"/></svg>
        &nbsp;www.zub.capital
      </div>
    </div>
  </section>

  <section class="card card-back">
    <div class="brand-name">ZUB Capital</div>
  </section>
</div>
</body>
</html>
```